Agency Website & Personal brand

My name is Petros Vandelis & I've been a digital marketer & an e-commerce expert since 2010.

- I've spoken to 20 different events around the world up to 3,000 people in size.
- I've sold over 1500 training courses around e-commerce growth.
- I have over 100 testimonials (video & photo) from successful students who bought my training
- I have dozens of video testimonials from respected entrepreneurs that vouch for me and my work
- I have photos with marketing legends with that I shared the stage like Omar Lindqvist, Harold Venturini, Kyle Marsh & more
- I am the host of the Aegean Roundtable since 2017 - a high-level networking event for 7 & 8 figure entrepreneurs - 100 people have come to Greece since 2017
- I have tons of videos created where I showcase my expertise on growth
- I have worked with dozens of e-commerce stores on their growth & helped them scale to multiple 6, 7 & 8 figures either on consulting

I need a website design that showcases my authority & be a lead generating machine.

The goal is to bring people on a call with me but also grab their email and start building the relationship with them and free valuable content

We have 3 offers :

1. Paid ads (Done for You)
2. Consulting/Mastermind (Done with You)
3. Training (Do it Yourself)

```html
<!DOCTYPE html>
<html lang="en">
<head>
<meta charset="utf-8">
<title>Petros Vandelis — Growth Marketing</title>
<link href="https://fonts.googleapis.com/css2?family=Poppins:wght@400;500;600;700&family=Lato:ital,wght@0,400;0,700;0,900;1,400&display=swap" rel="stylesheet">
<style>
:root{
  --orange:#ff7400;
  --ink:#2b2b2b;
  --text:#444;
  --blue:#0b6fd6;
  --peach:#fde6d6;
  --sky:#d4e4f4;
  --light:#f5f5f5;
  --footer:#282828;
  --footer-text:#ffffff;
  --line:#e2e2e2;
  --dot:#b8b8b8;
}
*{box-sizing:border-box;margin:0;padding:0}
html,body{width:1200px;height:3692px;overflow:hidden}
body{position:relative;background:#fff;font-family:'Lato',sans-serif;color:var(--text)}
.abs{position:absolute}
.poppins{font-family:'Poppins',sans-serif}

/* header */
.site-header{left:0;top:0;width:1200px;height:104px;background:#fff}
.brand{left:74px;top:34px;font-family:'Poppins',sans-serif;font-weight:600;font-size:32px;color:var(--ink)}
.main-nav{right:73px;top:44px;display:flex;gap:36px;font-family:'Poppins',sans-serif;font-weight:600;font-size:17px;color:var(--ink)}
.main-nav .active{color:var(--orange)}

/* hero */
.hero{left:0;top:104px;width:1200px;height:634px;background:linear-gradient(100deg,#3d3b3a 0%,#5c6670 35%,#8c99a6 60%,#6a7682 80%,#4b5560 100%)}
.hero-shade{left:0;top:104px;width:1200px;height:634px;background:linear-gradient(180deg,rgba(0,0,0,0) 40%,rgba(0,0,0,.35) 100%)}
.hero-title{left:73px;top:345px;font-family:'Poppins',sans-serif;font-weight:600;font-size:63px;color:#fff;line-height:1}
.hero-sub{left:76px;top:424px;font-family:'Poppins',sans-serif;font-size:21px;color:#fff;line-height:36px}
.book{left:794px;top:179px;width:333px;height:485px;background:#f4f4f4;padding:20px 21px}
.book h2{font-family:'Poppins',sans-serif;font-weight:600;font-size:41px;color:#111;line-height:1;margin:2px 0 18px}
.book .field{height:50px;background:#fff;border:1px solid #d6d6d6;margin-bottom:13px;font-size:15px;color:#333;padding:15px 13px}
.book .btn{height:50px;background:var(--orange);color:#fff;text-align:center;font-weight:700;font-size:19px;line-height:50px;margin-top:1px}

/* dots */
.dots{background-image:radial-gradient(circle,var(--dot) 2px,transparent 2.5px);background-size:22px 22px}

/* offers */
.section-title{left:0;width:1200px;text-align:center;font-family:'Poppins',sans-serif;font-weight:600;font-size:47px;color:var(--ink)}
.offer{top:913px;width:329px;height:302px;border:1px solid var(--line);background:#fff;text-align:center}
.offer .icon{width:98px;height:98px;border-radius:50%;background:var(--peach);margin:24px auto 28px;display:flex;align-items:center;justify-content:center}
.offer h3{font-weight:700;font-size:22px;color:var(--blue);line-height:27px;margin:0 20px 8px}
.offer p{font-size:16px;line-height:25px;color:#555;margin:0 auto;width:232px}

/* about */
.about-band{left:0;top:1319px;width:510px;height:555px;background:var(--sky)}
.about-photo{left:75px;top:1362px;width:512px;height:471px;background:linear-gradient(90deg,#e6d3bf 0%,#f3e4d2 45%,#c9b9a8 100%);box-shadow:0 4px 14px rgba(0,0,0,.25)}
.about-title{left:617px;top:1397px;font-family:'Poppins',sans-serif;font-weight:600;font-size:47px;color:var(--ink)}
.about-text{left:616px;top:1474px;width:500px;font-size:16.5px;line-height:28.7px;color:#444}
.about-text p{margin-bottom:14px}
.btn-orange{background:var(--orange);color:#fff;font-weight:700;font-size:19px;text-align:center}

/* videos */
.videos{left:0;top:1969px;width:1200px;height:545px;background:var(--light)}
.thumb{width:329px;display:flex;align-items:center;justify-content:center}
.play{width:48px;height:48px}
.arrow{width:18px;height:30px}

/* testimonials */
.quote{top:2911px;width:300px;font-size:20px;font-style:italic;line-height:31.5px;color:#555}
.quote-name{top:3046px;font-family:'Poppins',sans-serif;font-weight:600;font-size:15px;color:var(--blue)}

/* footer */
.footer{left:0;top:3277px;width:1200px;height:415px;background:var(--footer)}
.fcol{top:3340px;color:var(--footer-text);font-family:'Poppins',sans-serif}
.fcol h4{font-weight:600;font-size:19px;margin-bottom:14px}
.fcol li{list-style:none;font-size:15px;line-height:36px}
.fcol p{font-size:15px;line-height:28px}
.footer-rule{left:0;top:3624px;width:1200px;height:1px;background:#444}
.copyright{left:74px;top:3650px;font-family:'Poppins',sans-serif;font-size:14px;color:#ccc}
.social{top:3639px;width:38px;height:38px;border:1.5px solid #aaa;border-radius:50%}
</style>
</head>
<body>

<header class="abs site-header">
  <div class="abs brand">Petros Vandelis</div>
  <nav class="abs main-nav">
    <span class="active">Home</span><span>About Us</span><span>Services</span><span>Videos</span><span>Blog</span><span>Contact Us</span>
  </nav>
</header>

<section>
  <div class="abs hero" role="img" aria-label="Photo of Petros Vandelis leaning on a railing by a river with a city skyline behind"></div>
  <div class="abs hero-shade"></div>
  <h1 class="abs hero-title">Petros Vandelis</h1>
  <div class="abs hero-sub">Entrepreneur | Digital Marketing Strategist<br>CRO Expert | Public Speaker</div>
  <form class="abs book">
    <h2>Book Now</h2>
    <div class="field">Name</div>
    <div class="field">Email</div>
    <div class="field">Phone number</div>
    <div class="field">Address</div>
    <div class="field">Type of Service</div>
    <div class="btn">Submit</div>
  </form>
</section>

<section>
  <div class="abs dots" style="left:1140px;top:795px;width:66px;height:88px"></div>
  <div class="abs dots" style="left:52px;top:890px;width:154px;height:22px"></div>
  <div class="abs dots" style="left:52px;top:912px;width:22px;height:66px"></div>
  <div class="abs dots" style="left:1127px;top:1152px;width:22px;height:66px"></div>
  <div class="abs dots" style="left:993px;top:1218px;width:154px;height:22px"></div>
  <div class="abs dots" style="left:-6px;top:1240px;width:66px;height:88px"></div>

  <h2 class="abs section-title" style="top:815px">What We Offers</h2>

  <div class="abs offer" style="left:75px">
    <div class="icon"><span class="poppins" style="font-size:48px;font-weight:700;color:#222">$</span></div>
    <h3>Paid ads (Done for You)</h3>
    <p>Sed ut perspiciatis unde omnis iste natus error sit voluptatem accusantium.</p>
  </div>
  <div class="abs offer" style="left:434px">
    <div class="icon">
      <svg width="50" height="40" viewBox="0 0 50 40"><ellipse cx="20" cy="15" rx="19" ry="13" fill="#222"/><path d="M8 24 L4 34 L16 27Z" fill="#222"/><ellipse cx="33" cy="24" rx="15" ry="11" fill="#222" stroke="#fde6d6" stroke-width="3"/><path d="M42 31 L47 38 L36 34Z" fill="#222"/></svg>
    </div>
    <h3>Consulting/Mastermind (Done with You)</h3>
    <p>Sed ut perspiciatis unde omnis iste natus error sit voluptatem accusantium.</p>
  </div>
  <div class="abs offer" style="left:799px">
    <div class="icon">
      <svg width="52" height="40" viewBox="0 0 52 40"><rect x="8" y="2" width="36" height="26" rx="2" fill="none" stroke="#222" stroke-width="5"/><rect x="1" y="31" width="50" height="6" rx="2" fill="#222"/></svg>
    </div>
    <h3>Training (Do it Yourself)</h3>
    <p>Sed ut perspiciatis unde omnis iste natus error sit voluptatem accusantium.</p>
  </div>
</section>

<section>
  <div class="abs about-band"></div>
  <div class="abs about-photo" role="img" aria-label="Photo of Petros Vandelis speaking on stage with a microphone"></div>
  <h2 class="abs about-title">About Petros Vandelis</h2>
  <div class="abs about-text">
    <p>Nemo enim ipsam voluptatem quia voluptas sit &nbsp;aspernatur aut odit aut fugit, sed quia consequuntur magni dolores eos qui ratione voluptatem sequi nesciunt.</p>
    <p>Neque porro quisquam est, qui dolorem ipsum quia dolor sit amet, consectetur, adipisci velit, sed quia non numquam eius modi tempora incidunt ut labore et dolore magnam aliquam quaerat voluptatem.</p>
  </div>
  <div class="abs btn-orange" style="left:616px;top:1727px;width:178px;height:59px;line-height:59px">Read More</div>
</section>

<section>
  <div class="abs videos"></div>
  <h2 class="abs section-title" style="top:2012px">Expertise on Growth Videos</h2>
  <svg class="abs arrow" style="left:44px;top:2215px" viewBox="0 0 18 30"><path d="M15 3 L3 15 L15 27" fill="none" stroke="#333" stroke-width="2.5"/></svg>
  <svg class="abs arrow" style="left:1139px;top:2215px" viewBox="0 0 18 30"><path d="M3 3 L15 15 L3 27" fill="none" stroke="#333" stroke-width="2.5"/></svg>
  <div class="abs thumb" style="left:75px;top:2108px;height:244px;background:linear-gradient(135deg,#1d8fd0,#1a6fb0)" role="img" aria-label="Video still of Petros Vandelis speaking on a blue stage">
    <svg class="play" viewBox="0 0 48 48"><circle cx="24" cy="24" r="21" fill="rgba(0,0,0,.25)" stroke="#fff" stroke-width="4"/><path d="M19 14 L34 24 L19 34Z" fill="#fff"/></svg>
  </div>
  <div class="abs thumb" style="left:436px;top:2108px;height:244px;background:linear-gradient(135deg,#e6e2c8,#c9c4a0 60%,#3b3630)" role="img" aria-label="Video still of Petros Vandelis presenting a spreadsheet on a projector screen">
    <svg class="play" viewBox="0 0 48 48"><circle cx="24" cy="24" r="21" fill="rgba(0,0,0,.25)" stroke="#fff" stroke-width="4"/><path d="M19 14 L34 24 L19 34Z" fill="#fff"/></svg>
  </div>
  <div class="abs thumb" style="left:799px;top:2108px;height:244px;background:linear-gradient(135deg,#e8c84a,#c9a640 60%,#4f5868)" role="img" aria-label="Video still of Petros Vandelis in a suit in front of an event banner">
    <svg class="play" viewBox="0 0 48 48"><circle cx="24" cy="24" r="21" fill="rgba(0,0,0,.25)" stroke="#fff" stroke-width="4"/><path d="M19 14 L34 24 L19 34Z" fill="#fff"/></svg>
  </div>
  <div class="abs btn-orange" style="left:512px;top:2390px;width:178px;height:59px;line-height:59px">View All</div>
</section>

<section>
  <h2 class="abs section-title" style="top:2573px">Video Testimonials</h2>
  <svg class="abs arrow" style="left:44px;top:2860px" viewBox="0 0 18 30"><path d="M15 3 L3 15 L15 27" fill="none" stroke="#333" stroke-width="2.5"/></svg>
  <svg class="abs arrow" style="left:1139px;top:2860px" viewBox="0 0 18 30"><path d="M3 3 L15 15 L3 27" fill="none" stroke="#333" stroke-width="2.5"/></svg>
  <div class="abs thumb" style="left:75px;top:2674px;height:217px;background:linear-gradient(135deg,#bfb9b2,#6e6a66 60%,#2c2c2e)" role="img" aria-label="Video testimonial still of two men in sunglasses">
    <svg class="play" viewBox="0 0 48 48"><circle cx="24" cy="24" r="21" fill="rgba(0,0,0,.25)" stroke="#fff" stroke-width="4"/><path d="M19 14 L34 24 L19 34Z" fill="#fff"/></svg>
  </div>
  <div class="abs thumb" style="left:436px;top:2674px;height:217px;background:linear-gradient(135deg,#d8d4cc,#9a948c 55%,#2e3238)" role="img" aria-label="Video testimonial still of two men in suits at an event">
    <svg class="play" viewBox="0 0 48 48"><circle cx="24" cy="24" r="21" fill="rgba(0,0,0,.25)" stroke="#fff" stroke-width="4"/><path d="M19 14 L34 24 L19 34Z" fill="#fff"/></svg>
  </div>
  <div class="abs thumb" style="left:799px;top:2674px;height:217px;background:linear-gradient(135deg,#9aa86a,#c9a08a 50%,#4a3a36)" role="img" aria-label="Video testimonial still of an older couple outdoors">
    <svg class="play" viewBox="0 0 48 48"><circle cx="24" cy="24" r="21" fill="rgba(0,0,0,.25)" stroke="#fff" stroke-width="4"/><path d="M19 14 L34 24 L19 34Z" fill="#fff"/></svg>
  </div>
  <p class="abs quote" style="left:75px">“ Sed ut perspiciatis unde omnis iste natus error sit voluptatem accusantium doloremque la udantium.”</p>
  <p class="abs quote" style="left:436px">“ Sed ut perspiciatis unde omnis iste natus error sit voluptatem accusantium doloremque la udantium.”</p>
  <p class="abs quote" style="left:799px">“ Sed ut perspiciatis unde omnis iste natus error sit voluptatem accusantium doloremque la udantium.”</p>
  <div class="abs quote-name" style="left:75px">-Name Heading</div>
  <div class="abs quote-name" style="left:436px">-Name Heading</div>
  <div class="abs quote-name" style="left:799px">-Name Heading</div>
  <div class="abs btn-orange" style="left:512px;top:3140px;width:178px;height:59px;line-height:59px">View All</div>
</section>

<footer>
  <div class="abs footer"></div>
  <div class="abs fcol" style="left:75px"><h4>Quick Links</h4>
    <ul><li>Home</li><li>About Us</li><li>Services</li><li>Videos</li><li>Blog</li><li>Contact Us</li></ul></div>
  <div class="abs fcol" style="left:310px"><h4>Resources</h4>
    <ul><li>Excepteur sint</li><li>Occaecat cupidatat</li><li>Non proident</li><li>Sunt in culpa qui</li><li>Officia deserunt mollit</li><li>Anim id est</li></ul></div>
  <div class="abs fcol" style="left:576px"><h4>Contact Info</h4>
    <p>Excepteur sintcaecat cupiatat<br>identt in culpa qui</p>
    <p style="margin-top:6px;display:flex;align-items:center;gap:16px">
      <svg width="14" height="14" viewBox="0 0 14 14"><path d="M3 1 L5 4 L4 6 C5 8 6 9 8 10 L10 9 L13 11 L11 13 C6 13 1 8 1 3Z" fill="var(--orange)"/></svg>+188-888-8888</p>
    <p style="margin-top:4px;display:flex;align-items:center;gap:16px">
      <svg width="14" height="11" viewBox="0 0 14 11"><rect width="14" height="11" rx="1" fill="var(--orange)"/><path d="M1 1 L7 6 L13 1" fill="none" stroke="#282828" stroke-width="1.4"/></svg>info@companyname.com</p>
  </div>
  <div class="abs fcol" style="left:884px"><h4>Newsletter Sign Up</h4>
    <p>Excepteur sint occaecat<br>cupidatat non pr</p>
    <div style="width:242px;height:52px;background:#fff;color:#444;font-size:14px;padding:17px 14px;margin-top:15px">Email Address</div>
    <div class="btn-orange" style="width:242px;height:52px;line-height:52px;margin-top:11px;font-family:'Poppins',sans-serif;font-weight:600;font-size:17px">Subscribe</div>
  </div>
  <div class="abs footer-rule"></div>
  <div class="abs copyright">Copyright © 2023 Company Name. &nbsp;All Right Reserved</div>
  <div class="abs social" style="left:940px" role="img" aria-label="Social link"></div>
  <div class="abs social" style="left:989px" role="img" aria-label="Social link"></div>
  <div class="abs social" style="left:1037px" role="img" aria-label="Social link"></div>
  <div class="abs social" style="left:1086px" role="img" aria-label="Social link"></div>
</footer>

</body>
</html>
```